Marlow Estate Fixers (Handyman / Home Improvement Company)

Looking for a double sided professional looking business card with Logo attached to be highlighted on one side and throwing in an image of a handyman as an option would be nice to see as well. We are a company focused on providing quality Handyman and Home improvement services in a timely manner that is done right the first time with integrity

Industry/Entity Type

Handyman / Home Improvement

Contact Information for Business Card

(LOGO, Name, Mobile and office phone numbers, email) on front side of card, (the words "The SOLUTION to all of your Handyman and Home Improvement needs" followed by "Family Owned and Operated" at the very bottom) on the back.

Colors
EB3D1F
EC4F4E
F09395
F8D3D4
FCEDEE

Requirements
Must have
• Red, Gray, Black Color scheme
Should not have
• No Yellow or Blue colors

```html
<!DOCTYPE html>
<html lang="en">
<head>
<meta charset="utf-8">
<title>Marlow Estate Fixers – Business Card</title>
<link href="https://fonts.googleapis.com/css2?family=Poppins:wght@300;400;600;700&display=swap" rel="stylesheet">
<style>
  :root {
    --bg: #f1f1f1;
    --red: #ec2a2f;
    --charcoal: #222226;
    --charcoal-soft: #2b2b30;
    --white: #ffffff;
  }
  * { margin: 0; padding: 0; box-sizing: border-box; }
  html, body { width: 1200px; height: 990px; overflow: hidden; }
  body {
    background: var(--bg);
    font-family: "Poppins", sans-serif;
    position: relative;
  }
  .card {
    position: absolute;
    left: 244px;
    width: 712px;
    height: 406px;
    border-radius: 42px;
    overflow: hidden;
  }
  /* Brand side */
  .card--brand { top: 68px; background: var(--red); color: var(--white); }
  .brand-name {
    position: absolute;
    left: 0; right: 0; top: 118px;
    text-align: center;
    font-weight: 700;
    font-size: 46px;
    line-height: 1.1;
    letter-spacing: 1px;
    text-transform: uppercase;
  }
  .brand-tagline {
    position: absolute;
    left: 0; right: 0; top: 334px;
    text-align: center;
    font-weight: 400;
    font-size: 16px;
    line-height: 22px;
    letter-spacing: 0.3px;
  }
  /* Contact side */
  .card--contact { top: 516px; background: var(--charcoal); color: var(--white); }
  .contact-brand {
    position: absolute;
    left: 28px; top: 40px;
    width: 222px;
    text-align: center;
    font-weight: 700;
    font-size: 30px;
    line-height: 1.15;
    text-transform: uppercase;
    color: var(--white);
  }
  .person {
    position: absolute;
    right: 32px; top: 26px;
    text-align: right;
  }
  .person-name {
    font-size: 40px;
    line-height: 46px;
    color: var(--red);
    letter-spacing: 0.5px;
  }
  .person-name .first { font-weight: 700; }
  .person-name .last { font-weight: 300; }
  .person-title { font-size: 19px; font-weight: 400; margin-top: 2px; }
  .accent-bar {
    position: absolute;
    right: 0; top: 30px;
    width: 20px; height: 62px;
    background: var(--red);
  }
  .address {
    position: absolute;
    left: 26px; top: 214px;
    font-size: 19px;
    line-height: 26px;
    letter-spacing: 0.3px;
  }
  .contact-list {
    position: absolute;
    left: 26px; top: 283px;
    list-style: none;
    font-size: 19px;
    letter-spacing: 0.3px;
  }
  .contact-list li { display: flex; align-items: center; height: 24.3px; }
  .contact-list svg { width: 16px; height: 16px; margin-right: 10px; flex: none; }
  .contact-list .hl { color: var(--red); }
  .corner-disc {
    position: absolute;
    right: -40px; bottom: -120px;
    width: 270px; height: 270px;
    border-radius: 50%;
    background: var(--charcoal-soft);
  }
</style>
</head>
<body>

<section class="card card--brand">
  <h1 class="brand-name">Marlow Estate<br>Fixers</h1>
  <p class="brand-tagline">Family Owned and Operated<br>Your SOLUTION to all of your Handyman and Home Improvement needs</p>
</section>

<section class="card card--contact">
  <div class="corner-disc"></div>
  <p class="contact-brand">Marlow Estate Fixers</p>

  <div class="person">
    <h2 class="person-name"><span class="first">Dana</span> <span class="last">Kerrow</span></h2>
    <p class="person-title">Founder &amp; CEO</p>
  </div>
  <div class="accent-bar"></div>

  <p class="address">418 Elmstead Rd. Suite 12<br>Brookvale, TX 76540</p>

  <ul class="contact-list">
    <li>
      <svg viewBox="0 0 16 16"><rect x="4" y="1" width="8" height="14" rx="1.5" fill="none" stroke="#ec2a2f" stroke-width="1.5"/><circle cx="8" cy="12.5" r="0.8" fill="#ec2a2f"/></svg>
      (555) 204-3186
    </li>
    <li>
      <svg viewBox="0 0 16 16"><path d="M3 2l3 0 1 3-2 1.5c.8 1.8 2.2 3.2 4 4L10.5 8.5l3 1v3c0 .8-.7 1.5-1.5 1.5C6.5 14 2 9.5 2 4c0-1 .5-2 1-2z" fill="#ec2a2f"/></svg>
      (555) 318-6620
    </li>
    <li>
      <svg viewBox="0 0 16 16"><circle cx="8" cy="8" r="6.5" fill="none" stroke="#ec2a2f" stroke-width="1.5"/><path d="M1.5 8h13M8 1.5c-2.5 3-2.5 10 0 13M8 1.5c2.5 3 2.5 10 0 13" fill="none" stroke="#ec2a2f" stroke-width="1.2"/></svg>
      www.<span class="hl">marlowfixers</span>.com
    </li>
    <li>
      <svg viewBox="0 0 16 16"><rect x="1.5" y="4" width="13" height="9" rx="1" fill="none" stroke="#ec2a2f" stroke-width="1.5"/><path d="M1.5 4.5L8 9.5l6.5-5" fill="none" stroke="#ec2a2f" stroke-width="1.5"/></svg>
      info@<span class="hl">marlowfixers</span>.com
    </li>
  </ul>
</section>

</body>
</html>
```